TA BRAMLEY BUSINESS CARD DESIGN PROJECT

We need to utilize our logo that was expertly created on PixelHarbor and now need to match this with a business card design.

```html
<!DOCTYPE html>
<html lang="en">
<head>
<meta charset="UTF-8">
<title>TA BRAMLEY Business Cards</title>
<link href="https://fonts.googleapis.com/css2?family=Montserrat:wght@400;700&display=swap" rel="stylesheet">
<style>
  :root {
    --brand-blue: #0f56a8;
    --card-white: #ffffff;
    --ink: #2a2a2a;
    --backdrop: #d9c9ad;
  }
  * { margin: 0; padding: 0; box-sizing: border-box; }
  html, body { width: 1200px; height: 900px; overflow: hidden; }
  body {
    background: var(--backdrop);
    font-family: "Montserrat", sans-serif;
    position: relative;
  }
  .card {
    position: absolute;
    left: 310px;
    width: 582px;
    height: 332px;
    border-radius: 28px;
    overflow: hidden;
    box-shadow: 0 4px 14px rgba(0,0,0,0.22);
  }
  .card--front { top: 86px; background: var(--card-white); }
  .card--back { top: 470px; background: var(--brand-blue); }

  .wordmark {
    position: absolute;
    left: 0; right: 0;
    text-align: center;
    font-weight: 700;
    letter-spacing: 4px;
    white-space: nowrap;
  }
  .card--front .wordmark { top: 62px; font-size: 60px; color: var(--brand-blue); }
  .card--back .wordmark { top: 128px; font-size: 64px; color: var(--card-white); }

  .holder {
    position: absolute;
    top: 193px; left: 0; right: 0;
    text-align: center;
  }
  .holder__name { font-weight: 700; font-size: 20px; color: var(--brand-blue); letter-spacing: 0.3px; line-height: 1.2; }
  .holder__role { font-size: 14px; color: var(--ink); line-height: 1.4; }

  .contact-address {
    position: absolute;
    top: 262px; right: 302px;
    text-align: right;
    font-size: 14.5px; line-height: 20px; color: var(--ink);
  }
  .contact-divider {
    position: absolute;
    top: 252px; left: 291px;
    width: 2px; height: 54px;
    background: var(--brand-blue);
  }
  .contact-list {
    position: absolute;
    top: 250px; left: 304px;
    list-style: none;
    font-size: 14.5px; line-height: 19.5px; color: var(--ink);
  }
  .contact-list li { display: flex; align-items: center; gap: 6px; }
  .contact-list svg { width: 12px; height: 12px; fill: var(--brand-blue); flex: none; }
  .edge-band {
    position: absolute;
    left: 0; right: 0; bottom: 0;
    height: 10px;
    background: var(--brand-blue);
  }
</style>
</head>
<body>
  <section class="card card--front">
    <div class="wordmark">TA BRAMLEY</div>
    <div class="holder">
      <p class="holder__name">DANIEL ASHFORD</p>
      <p class="holder__role">Managing Director</p>
    </div>
    <p class="contact-address">Your address, City<br>State, Zip 1234</p>
    <div class="contact-divider"></div>
    <ul class="contact-list">
      <li><svg viewBox="0 0 12 12"><path d="M1 4c0-2 10-2 10 0v1H8V4H4v1H1z M2 6h8l1 5H1z"/></svg>123 456 789</li>
      <li><svg viewBox="0 0 12 12"><path d="M1 3h10v1L6 7 1 4z M1 5l5 3 5-3v4H1z"/></svg>info@tabramley.com</li>
      <li><svg viewBox="0 0 12 12"><circle cx="6" cy="6" r="5.5"/><path d="M3 4l2 1 1 2-2 1z M7 2l2 2-1 2z" fill="#fff"/></svg>www.tabramley.com</li>
    </ul>
    <div class="edge-band"></div>
  </section>

  <section class="card card--back">
    <div class="wordmark">TA BRAMLEY</div>
  </section>
</body>
</html>
```